OBK Farcoast Logistics Limited

We need the buissnes card to be very exclusive. As we are all young in our company. We need this to be the gate to make our clients feel deep interest for us.

We are focused in as International Trade advisors, and our products go from Oil Tanker Ships to Rubber balls for dogs.

Our Slogan is Bringing Ports Home.
And our main marketing will be through Internet.

We were stablished in 2009 In Mexico and we also have offices in Hong Kong.
We have representatives in China and Europe.

Target Market(s)

Is every company or Individual that wants to develop an International Project or product development or Logistic service of Goods and people.
Some of our current projects are Ship Brokerage, Mine Brokerage, Real State and Product Pormotional development.

Industry/Entity Type

It Company

Requirements
Must have
• Our Logo and slogan, and make the card accoriding to the logo.
Nice to have
• Our Colors

```html
<!DOCTYPE html>
<html lang="en">
<head>
<meta charset="utf-8">
<title>OBK — Business Card</title>
<link rel="stylesheet" href="https://fonts.googleapis.com/css2?family=Source+Sans+3:wght@400;600;700&display=swap">
<style>
  :root {
    --stage: #e4e4e8;
    --card: #232323;
    --green: #8cc63f;
    --blue: #1b82bd;
    --white: #ffffff;
    --divider: #9a9a9a;
  }
  * { margin: 0; padding: 0; box-sizing: border-box; }
  html, body { width: 1200px; height: 987px; overflow: hidden; }
  body {
    background: var(--stage);
    font-family: "Source Sans 3", "Helvetica Neue", Arial, sans-serif;
    position: relative;
  }
  .card {
    position: absolute;
    width: 700px;
    height: 400px;
    border-radius: 28px;
    background: var(--card);
    overflow: hidden;
    box-shadow: 0 10px 24px rgba(0,0,0,0.18);
  }
  .card--back { left: 440px; top: 60px; }
  .card--front { left: 60px; top: 527px; }

  /* Back */
  .back-brand {
    position: absolute;
    left: 0; right: 0; top: 120px;
    display: flex; align-items: center; justify-content: center; gap: 22px;
  }
  .back-brand__dot {
    width: 46px; height: 46px; border-radius: 50%;
    background: var(--blue);
  }
  .back-brand__name {
    color: var(--green);
    font-size: 96px; font-weight: 700; letter-spacing: 4px; line-height: 1;
  }
  .back-web {
    position: absolute; left: 0; right: 0; bottom: 62px;
    text-align: center;
    font-size: 22px; letter-spacing: 6px; color: var(--white);
  }
  .back-web span { color: var(--blue); }

  /* Front */
  .front-wave { position: absolute; inset: 0; }
  .front-brand {
    position: absolute; left: 150px; top: 60px; width: 210px;
    text-align: center;
  }
  .front-brand__name {
    display: inline-flex; align-items: center; gap: 12px;
    color: var(--green); font-size: 72px; font-weight: 700; line-height: 1; letter-spacing: 2px;
  }
  .front-brand__dot { width: 22px; height: 22px; border-radius: 50%; background: var(--blue); }
  .front-brand__slogan {
    margin-top: 6px; color: var(--blue); font-size: 15px; letter-spacing: 0.5px;
  }
  .divider {
    position: absolute; left: 390px; top: 55px; width: 2px; height: 135px;
    background: linear-gradient(to bottom, transparent, var(--divider), transparent);
  }
  .person { position: absolute; left: 418px; top: 48px; }
  .person__name { color: var(--green); font-size: 32px; font-weight: 700; line-height: 1.05; }
  .person__role { color: var(--blue); font-size: 20px; }
  .contacts {
    position: absolute; left: 418px; top: 135px;
    list-style: none;
  }
  .contacts li {
    display: flex; align-items: center; gap: 12px;
    color: var(--white); font-size: 21px; line-height: 30px;
  }
  .contacts svg { width: 18px; height: 18px; flex: none; }
  .address {
    position: absolute; left: 38px; top: 262px;
    color: var(--white); font-size: 19px; line-height: 24px; font-style: normal;
  }
</style>
</head>
<body>

<section class="card card--back" aria-label="Card back">
  <div class="back-brand">
    <span class="back-brand__dot"></span>
    <span class="back-brand__name">OBK</span>
  </div>
  <p class="back-web">www.<span>obkbridgeway</span>.com</p>
</section>

<section class="card card--front" aria-label="Card front">
  <svg class="front-wave" viewBox="0 0 700 400" preserveAspectRatio="none" aria-hidden="true">
    <path d="M0 225 C120 200 220 270 330 320 C430 365 560 372 700 362 L700 400 L0 400 Z" fill="var(--blue)"/>
    <path d="M0 214 C120 190 225 258 335 308 C435 352 565 362 700 352" fill="none" stroke="var(--green)" stroke-width="5"/>
  </svg>

  <div class="front-brand">
    <div class="front-brand__name"><span class="front-brand__dot"></span>OBK</div>
    <p class="front-brand__slogan">Bringing Ports Home</p>
  </div>

  <div class="divider"></div>

  <div class="person">
    <p class="person__name">Your Name</p>
    <p class="person__role">Position</p>
  </div>

  <ul class="contacts">
    <li>
      <svg viewBox="0 0 20 20"><circle cx="10" cy="10" r="9.5" fill="var(--green)"/><path d="M7 5.5l2 2.2-1.1 1.3c.7 1.4 1.7 2.4 3.1 3.1l1.3-1.1 2.2 2-1.2 1.6C9.6 14.3 5.7 10.4 5.4 6.7z" fill="var(--card)"/></svg>
      123-456-7890
    </li>
    <li>
      <svg viewBox="0 0 20 20"><rect x="5.5" y="1.5" width="9" height="17" rx="1.5" fill="var(--green)"/><rect x="7" y="4" width="6" height="7" fill="var(--card)"/><circle cx="10" cy="15" r="1.3" fill="var(--card)"/></svg>
      123-456-7890
    </li>
    <li>
      <svg viewBox="0 0 20 20"><rect x="1" y="4" width="18" height="12" rx="1.5" fill="var(--green)"/><path d="M2 5l8 6 8-6" fill="none" stroke="var(--card)" stroke-width="1.6"/></svg>
      info@obkbridgeway.com
    </li>
    <li>
      <svg viewBox="0 0 20 20"><circle cx="10" cy="10" r="9" fill="var(--green)"/><g fill="none" stroke="var(--card)" stroke-width="1.2"><ellipse cx="10" cy="10" rx="4" ry="9"/><path d="M1 10h18M2.5 5.5h15M2.5 14.5h15"/></g></svg>
      www.obkbridgeway.com
    </li>
  </ul>

  <address class="address">
    00, Complex Name<br>City, State, 00045
  </address>
</section>

</body>
</html>
```